Professional Website

We are looking for a new website for our Staffing Company. Attached is a document with all the details and pages needed along with some examples of others websites.

We want a professional Look and feel around the same color theme as the attached Amber Compass.

We currently host our site on PageLoom.io. If the winning designer can also add to PageLoom, that is a plus.

```html
<!DOCTYPE html>
<html lang="en">
<head>
<meta charset="utf-8">
<title>Talentline – Staffing</title>
<link href="https://fonts.googleapis.com/css2?family=Rubik:wght@500;700&family=Roboto:wght@400;500&display=swap" rel="stylesheet">
<style>
:root{
  --brand:#2438b8;
  --brand-dark:#1a2a8f;
  --navy:#030726;
  --ink:#111;
  --white:#fff;
}
*{margin:0;padding:0;box-sizing:border-box}
html,body{width:1064px;height:1200px;overflow:hidden;background:var(--white)}
body{position:relative;font-family:'Roboto',sans-serif;color:var(--ink)}
.abs{position:absolute}
.utility{top:0;left:0;width:1064px;height:38px}
.utility-links{left:292px;top:0;height:38px;display:flex;align-items:center;gap:34px;color:var(--white);font-size:13.5px;font-weight:500}
.utility-links span{display:flex;align-items:center;gap:9px;white-space:nowrap}
.utility-phone{left:836px;top:0;width:131px;height:38px;background:var(--brand-dark);color:var(--white);display:flex;align-items:center;justify-content:center;gap:7px;font-size:13.5px;font-weight:500}
.logo{font-family:'Rubik',sans-serif;font-weight:700;color:var(--brand);font-size:31px;letter-spacing:-.5px;white-space:nowrap}
.site-logo{left:99px;top:47px}
.main-nav{left:305px;top:59px;display:flex;gap:19px;font-size:12.5px;text-transform:uppercase;white-space:nowrap}
.main-nav a{color:var(--ink);text-decoration:none}
.main-nav a.active{color:var(--brand);font-weight:500}
.nav-social{left:836px;top:52px;display:flex;gap:4px}
.nav-social i{display:block;width:29px;height:29px;border:1.5px solid var(--ink);border-radius:50%}
.hero{top:105px;width:532px;height:439px;color:var(--white);text-align:center;display:flex;flex-direction:column;align-items:center;justify-content:center}
.hero-jobs{left:0;background:linear-gradient(160deg,#3448c4,#2a3cb6 60%,#3a4fc6)}
.hero-employers{left:532px;background:linear-gradient(135deg,#6e6a66,#b3aca2 45%,#8f877c 75%,#c9c0b3)}
.hero h2{font-family:'Rubik',sans-serif;font-weight:700;font-size:35px;text-transform:uppercase;margin-top:-12px;white-space:nowrap}
.hero p{font-size:13.7px;line-height:23px;width:420px;margin-top:8px}
.btn{display:inline-flex;align-items:center;gap:8px;font-family:'Roboto',sans-serif;font-weight:500;font-size:13.5px;text-transform:uppercase;color:var(--white)}
.btn-outline{border:2px solid var(--white);border-radius:3px;padding:0 14px;height:44px;margin-top:18px}
.about{top:544px;left:0;width:1064px;height:399px;background:linear-gradient(180deg,#fafafb,#eef0f4 40%,#e6e8ee);text-align:center}
.about h2{font-family:'Roboto',sans-serif;font-weight:500;font-size:29px;margin-top:72px}
.about p{width:750px;margin:16px auto 0;font-size:13.4px;line-height:22.8px;text-align:justify;text-align-last:center}
.btn-solid{background:var(--brand);height:44px;padding:0 15px;border-radius:2px;margin-top:25px}
.footer{top:943px;left:0;width:1064px;height:215px;background:var(--navy);color:var(--white)}
.footer .logo{color:var(--white);position:absolute;left:99px;top:58px}
.footer-social{left:99px;top:128px;display:flex;gap:8px}
.footer-social i{display:block;width:29px;height:29px;border:1.5px solid var(--white)}
.footer-col{top:64px}
.footer-col h3{font-size:13.5px;font-weight:500;text-transform:uppercase;margin-bottom:12px;white-space:nowrap}
.footer-col li{list-style:none;font-size:13.5px;height:30.5px;display:flex;align-items:center;gap:14px;white-space:nowrap}
.contact-row{display:flex;align-items:center;gap:10px;font-size:13px;margin-bottom:18px;white-space:nowrap}
.contact-row i{width:29px;height:29px;border:1.5px solid var(--white);border-radius:50%;display:flex;align-items:center;justify-content:center}
.copyright{top:1158px;left:0;width:1064px;height:42px;background:var(--brand);color:var(--white);font-size:12px;display:flex;align-items:center;justify-content:center}
</style>
</head>
<body>

<svg class="abs utility" viewBox="0 0 1064 38" aria-hidden="true">
  <path d="M243 0 C262 0 268 38 300 38 L1064 38 L1064 0 Z" fill="#2438b8"/>
</svg>
<div class="abs utility-links">
  <span><svg width="12" height="13" viewBox="0 0 12 13"><circle cx="6" cy="3.5" r="3.2" fill="#fff"/><path d="M0 13c0-4 2.5-6 6-6s6 2 6 6z" fill="#fff"/></svg>Employee Login</span>
  <span>|</span>
  <span><svg width="12" height="13" viewBox="0 0 12 13"><circle cx="6" cy="3.5" r="3.2" fill="#fff"/><path d="M0 13c0-4 2.5-6 6-6s6 2 6 6z" fill="#fff"/></svg>Wage Card Login</span>
  <span>|</span>
  <span><svg width="12" height="13" viewBox="0 0 12 13"><circle cx="6" cy="3.5" r="3.2" fill="#fff"/><path d="M0 13c0-4 2.5-6 6-6s6 2 6 6z" fill="#fff"/></svg>Bank Portal Login</span>
</div>
<div class="abs utility-phone">
  <svg width="13" height="13" viewBox="0 0 24 24"><path fill="#fff" d="M6.6 10.8a15 15 0 0 0 6.6 6.6l2.2-2.2a1 1 0 0 1 1-.25 11.4 11.4 0 0 0 3.6.57 1 1 0 0 1 1 1V20a1 1 0 0 1-1 1A17 17 0 0 1 3 4a1 1 0 0 1 1-1h3.5a1 1 0 0 1 1 1c0 1.25.2 2.45.57 3.57a1 1 0 0 1-.25 1z"/></svg>
  555-014-2200
</div>

<div class="abs logo site-logo">Talentline</div>
<nav class="abs main-nav">
  <a class="active" href="#">Home</a>
  <a href="#">Looking for a job</a>
  <a href="#">Looking for employees</a>
  <a href="#" style="margin-left:3px">Office information</a>
</nav>
<div class="abs nav-social" aria-label="Social links"><i></i><i></i><i></i><i></i></div>

<section class="abs hero hero-jobs" role="img" aria-label="Photo of hands signing a document, tinted blue">
  <h2>I’m looking for a job</h2>
  <p>To change the way temporary staffing agencies fill orders.We only work with the best companies and best employees.</p>
  <span class="btn btn-outline">Learn more
    <svg width="13" height="13" viewBox="0 0 16 16"><circle cx="8" cy="8" r="8" fill="#fff"/><path d="M5 8h5M8 5l3 3-3 3" stroke="#2a3cb6" stroke-width="2" fill="none"/></svg></span>
</section>
<section class="abs hero hero-employers" role="img" aria-label="Photo of candidates waiting with résumés and phones">
  <h2>I need employees</h2>
  <p>We’re the first and only recruiting agency specializing in long-term temporary and direct hire staffing.</p>
  <span class="btn btn-outline">Learn more
    <svg width="13" height="13" viewBox="0 0 16 16"><circle cx="8" cy="8" r="8" fill="#fff"/><path d="M5 8h5M8 5l3 3-3 3" stroke="#8f877c" stroke-width="2" fill="none"/></svg></span>
</section>

<section class="abs about" role="img" aria-label="Faded photo of a business handshake behind the about text">
  <h2>ABOUT US</h2>
  <p>Greatest part of our daily job is that we are constantly bringing people together. Our Clients come to us in search of the perfect candidate and the job hunters approach us when they are inneed of a job or looking for their next exciting role.Being able to work with and connect the two is incredibly satisfying. Not to mention that in today's current job market, employers are fighting for the top talent. This makes our employees and partners grateful for the help in finding it!</p>
  <span class="btn btn-solid">Learn more
    <svg width="13" height="13" viewBox="0 0 16 16"><circle cx="8" cy="8" r="8" fill="#fff"/><path d="M5 8h5M8 5l3 3-3 3" stroke="#2438b8" stroke-width="2" fill="none"/></svg></span>
</section>

<footer class="abs footer">
  <div class="logo">Talentline</div>
  <div class="abs footer-social" aria-label="Social links"><i></i><i></i><i></i><i></i></div>
  <div class="abs footer-col" style="left:394px">
    <h3>Quicklinks</h3>
    <ul><li>»&nbsp; Home</li><li>»&nbsp; About Us</li><li>»&nbsp; Contact Us</li></ul>
  </div>
  <div class="abs footer-col" style="left:580px">
    <h3>Areas we service</h3>
    <ul><li>»&nbsp; Northfield</li><li>»&nbsp; Riverbend</li><li>»&nbsp; Oak Hollow</li></ul>
  </div>
  <div class="abs footer-col" style="left:801px">
    <h3>Contact us</h3>
    <div class="contact-row"><i><svg width="12" height="12" viewBox="0 0 24 24"><path fill="#fff" d="M6.6 10.8a15 15 0 0 0 6.6 6.6l2.2-2.2a1 1 0 0 1 1-.25 11.4 11.4 0 0 0 3.6.57 1 1 0 0 1 1 1V20a1 1 0 0 1-1 1A17 17 0 0 1 3 4a1 1 0 0 1 1-1h3.5a1 1 0 0 1 1 1c0 1.25.2 2.45.57 3.57a1 1 0 0 1-.25 1z"/></svg></i>555-014-2200</div>
    <div class="contact-row"><i><svg width="12" height="10" viewBox="0 0 12 10"><rect width="12" height="10" rx="1" fill="#fff"/><path d="M0.5 1l5.5 4 5.5-4" stroke="#030726" fill="none"/></svg></i>hello@talentline-staffing.com</div>
  </div>
</footer>
<div class="abs copyright">©&nbsp; 2022 Talentline All Right Reserved.</div>

</body>
</html>
```